Detail Shop Business card design

i need a business card design for my new detailing company called 'Brisk's Polish Works'. i want an all black and white design . simple, direct and to the point. i want the designer to choose a fitting font to match the logothe front should have logo, address, phone and email and the back side should have a slogan and text indicating that we offer services on anything including cars, trucks, motorcycles and RVs. slogan will read "we bring shine to every drive"
maybe also very small on the back side the IG icon with Brisks_Polish_Works

phone 208.417.6352
address 3847 E Larkin Ave
Marlow Falls OR 97412
email: BrisksPolish@mailvexo.com

Target Market(s)

all ages , auto enthusiasts

Industry/Entity Type

Automotive

Contact Information for Business Card

the front should have logo, address, phone and email and the back side should have a slogan and text indicating that we offer services on anything including cars, trucks, motorcycles and RVs. slogan will read "we bring shine to every drive"

phone 208.417.6352
address 3847 E Larkin Ave
Marlow Falls OR 97412

Colors
000000
ffffff

Requirements
Must have
• bold font and very simple design with good spacing
Nice to have
• anything creative from the designer indicating we service any types of vehicles
Should not have
• any colors ,

```html
<!DOCTYPE html>
<html lang="en">
<head>
<meta charset="utf-8">
<title>Brisk's Polish Works — Business Card</title>
<link rel="stylesheet" href="https://fonts.googleapis.com/css2?family=Lato:wght@400;700;900&display=swap">
<style>
  :root {
    --ink: #000000;
    --paper: #ffffff;
    --backdrop: #d9d9d9;
    --text-dark: #111111;
  }
  * { box-sizing: border-box; margin: 0; padding: 0; }
  html, body {
    width: 1200px;
    height: 880px;
    overflow: hidden;
    background: var(--backdrop);
    font-family: "Lato", Arial, sans-serif;
  }
  .canvas {
    position: relative;
    width: 1200px;
    height: 880px;
  }
  .card {
    position: absolute;
    left: 267px;
    width: 666px;
    height: 380px;
    border-radius: 26px;
    overflow: hidden;
  }
  .card--front {
    top: 40px;
    background: var(--ink);
    color: var(--paper);
  }
  .card--back {
    top: 460px;
    background: var(--paper);
    color: var(--text-dark);
  }

  /* Front: name mark + slogan */
  .brand {
    position: absolute;
    top: 110px;
    left: 0;
    right: 0;
    display: flex;
    align-items: center;
    justify-content: center;
    gap: 18px;
  }
  .brand__dot {
    width: 22px;
    height: 22px;
    border-radius: 50%;
    background: var(--paper);
  }
  .brand__name {
    font-weight: 900;
    font-size: 44px;
    letter-spacing: 1px;
    color: var(--paper);
  }
  .slogan {
    position: absolute;
    top: 232px;
    left: 0;
    right: 0;
    text-align: center;
    font-weight: 400;
    font-size: 19px;
    letter-spacing: 5px;
    color: var(--paper);
  }

  /* Back: contact block */
  .edge-tab {
    position: absolute;
    left: 0;
    top: 262px;
    width: 34px;
    height: 118px;
    background: var(--ink);
  }
  .contact {
    position: absolute;
    left: 70px;
    bottom: 34px;
    font-size: 19px;
    line-height: 1.2;
    color: var(--text-dark);
  }
  .contact__address { margin-bottom: 10px; }
  .contact__line {
    display: flex;
    align-items: center;
    gap: 8px;
  }
  .contact__icon {
    width: 16px;
    height: 16px;
    flex: none;
  }
</style>
</head>
<body>
<main class="canvas">
  <section class="card card--front" aria-label="Card front">
    <div class="brand">
      <span class="brand__dot"></span>
      <span class="brand__name">Brisk's Polish Works</span>
    </div>
    <p class="slogan">we bring shine to every drive</p>
  </section>

  <section class="card card--back" aria-label="Card back">
    <div class="edge-tab"></div>
    <div class="contact">
      <p class="contact__address">3847 E Larkin Ave<br>Marlow Falls OR 97412</p>
      <p class="contact__line">
        <svg class="contact__icon" viewBox="0 0 16 16" aria-hidden="true">
          <rect x="3" y="1" width="10" height="14" rx="1.5" fill="none" stroke="#111" stroke-width="1.6"/>
          <line x1="6.5" y1="12.5" x2="9.5" y2="12.5" stroke="#111" stroke-width="1.4"/>
        </svg>
        208.417.6352
      </p>
      <p class="contact__line">
        <svg class="contact__icon" viewBox="0 0 16 16" aria-hidden="true">
          <rect x="1" y="3" width="14" height="10" fill="#111"/>
          <polyline points="1.5,3.5 8,9 14.5,3.5" fill="none" stroke="#fff" stroke-width="1.3"/>
        </svg>
        BrisksPolish@mailvexo.com
      </p>
    </div>
  </section>
</main>
</body>
</html>
```